Mayhon online ordering platform looking for a great web design

Mayhon - from the Vietnamese words Mây Hồng meaning financial success.
Background
Mayhon is an online ordering platform for small retail businesses (corner stores). The idea is that small retailers will use the website to order their supplies. From this we will utilise the group buying to get better deals for them that they could not achieve individually.
We are looking for a simple but stylish design for our ordering page. The layout needs to be efficient, logical and self explanatory.
Products to be sold on the site are FMCG (fast moving consumer goods). Potential to be 000's of items.
Considerations
- end users are not technologically adept.
- Users are generally older so small print will not be well received.
- Use of touch screen monitors to select/change items so spacing in design is vital.
- Logical display of category and sub-categories.
- Easy selection of products to order as well as modification of quantity.
- Shopping cart with easy change of item quantity.
- List of items for ordering can be paginated.
- Items listed will have image for easy identification.
- Search box
- Format should be in psd (photoshop) or complete html/css
- All this information needs to be displayed on the one page.
Product information to contain the following:
- Image
- Price
- Product name
- Size
Area for prominent display of specials without crowding the product information.

```html
<!DOCTYPE html>
<html lang="en">
<head>
<meta charset="utf-8">
<title>Mayhon – Sub Category</title>
<link href="https://fonts.googleapis.com/css2?family=Ubuntu:wght@400;500;700&display=swap" rel="stylesheet">
<style>
:root{
  --accent:#f0542a;
  --accent-dark:#d9431c;
  --text:#555;
  --line:#ddd;
  --bar-top:#f8f5ea;
  --bar-bottom:#ece5cf;
  --bar-edge:#e0d8bf;
  --black:#0d0d0d;
  --teal:#1bb9c4;
}
*{box-sizing:border-box;margin:0;padding:0}
html,body{width:960px;height:1200px;overflow:hidden;background:#fff;font-family:'Ubuntu',sans-serif;color:var(--text)}
.topline{position:absolute;left:0;top:0;width:960px;height:11px;background:var(--black)}
.page{position:absolute;left:103px;top:0;width:753px;height:1200px;overflow:hidden}
.logo{position:absolute;top:37px;left:0;font-size:26px;color:#999;letter-spacing:.5px;display:flex;align-items:center;gap:8px}
.logo .mark{width:14px;height:14px;background:#999}

.bar{position:absolute;left:0;width:753px;height:28px;background:linear-gradient(var(--bar-top),var(--bar-bottom));border:1px solid var(--bar-edge);display:flex;align-items:stretch;font-size:12px;white-space:nowrap}
.bar a{color:#666;text-decoration:none;display:flex;align-items:center;padding:0 8px;position:relative}
.bar a::after{content:"";position:absolute;right:0;top:7px;bottom:7px;border-right:1px solid #d6ceb4}
.bar a.active{background:var(--accent);color:#fff;font-weight:500;font-size:13px}
.bar a.active::after{display:none}
.mainnav{top:92px}
.mainnav a{padding:0 18px}
.mainnav a.active{width:79px;justify-content:center;padding:0}
.search{position:absolute;right:3px;top:3px;width:170px;height:20px;background:#fff;border:1px solid #ddd;font-size:11px;font-style:italic;color:#888;padding:2px 8px}
.catnav{top:284px}
.subnav{top:314px;font-size:11.5px}
.subnav a{padding:0 7px}

.panel{position:absolute;top:124px;height:155px;border:1px solid var(--line);padding:5px}
.promo{left:0;width:502px}
.promo .art{width:100%;height:100%;background:linear-gradient(90deg,#e6dcd6 0 28%,var(--teal) 48%);position:relative;overflow:hidden}
.promo .deal{position:absolute;left:262px;top:22px;color:#fff;font-weight:700;font-size:76px;letter-spacing:-2px;line-height:1}
.promo .more{position:absolute;right:6px;bottom:5px;background:#f4f4f4;border:1px solid #ccc;font-size:11px;color:#666;padding:5px 8px}
.account{left:504px;width:249px}
.account .inner{display:flex;height:100%;background:var(--black)}
.account .portrait{width:98px;background:linear-gradient(#8a5a3c,#3a2a22)}
.account .info{flex:1;padding:9px 6px;color:#fff;position:relative}
.info h3{font-size:13px;font-weight:400;margin-bottom:3px}
.info .link{display:block;color:var(--accent);font-size:10px;line-height:12px}
.info .cart{position:absolute;top:79px;left:6px;font-size:12px}
.info .items{position:absolute;top:82px;left:72px;font-size:9px;line-height:12px}
.items em{color:var(--accent)}
.checkout{position:absolute;left:6px;right:4px;bottom:5px;height:17px;background:var(--accent);color:#fff;font-size:10px;display:flex;align-items:center;justify-content:center}

.crumbs{position:absolute;top:351px;left:2px;font-size:10px;color:#444}
.crumbs span{color:var(--accent)}
.title{position:absolute;top:364px;left:2px;font-size:22px;font-weight:500;color:var(--accent)}

.section{position:absolute;left:0;width:753px;border:1px solid var(--line);padding:0 10px;overflow:hidden}
.section h2{font-size:15px;font-weight:400;color:var(--accent);height:32px;line-height:38px;border-bottom:1px solid var(--line)}
.section h2 small{font-size:10px;color:#666}
.featured{top:398px;height:233px}
.latest{top:637px;height:563px;border-bottom:0}
.row{display:grid;grid-template-columns:repeat(5,1fr);height:199px;border-bottom:1px solid var(--line);padding:8px 0}
.item{border-right:1px solid var(--line);padding:0 10px}
.item:last-child{border-right:0}
.shot{height:116px;display:flex;justify-content:center;align-items:flex-end}
.bottle{width:46px;height:110px;border-radius:16px 16px 8px 8px}
.green{background:linear-gradient(90deg,#2da52a,#5fd04a,#2da52a)}
.blue{background:linear-gradient(#1c3fa0 0 22%,#f2f4f8 22%);width:44px}
.white{background:linear-gradient(90deg,#d9dde0,#fff,#d9dde0);width:50px}
.pink{background:linear-gradient(90deg,#d21f53,#f04a7a,#c2184a);width:38px}
.name{font-size:12px;font-weight:500;color:var(--accent);margin-top:5px;line-height:14px}
.meta{display:flex;justify-content:space-between;font-size:12px;color:#555;margin-top:2px;line-height:14px}
.order{display:flex;gap:3px;margin-top:6px;height:26px}
.qty-btn,.qty,.add{height:26px;border:1px solid #ccc;background:#f6f3ea;color:#555;font:500 14px 'Ubuntu',sans-serif;display:flex;align-items:center;justify-content:center}
.qty-btn{width:24px}
.qty{width:30px;background:#fff;font-size:12px}
.add{flex:1;min-width:30px;background:var(--accent);border-color:var(--accent-dark);margin-left:3px}
.add svg{width:16px;height:16px}
</style>
</head>
<body>
<div class="topline"></div>
<div class="page">
  <div class="logo"><span class="mark"></span>Mayhon</div>

  <nav class="bar mainnav">
    <a class="active">Home</a><a>About</a><a>Categories</a><a>How it works</a><a>Contact Us</a><a>Support</a>
    <div class="search">search</div>
  </nav>

  <div class="panel promo">
    <div class="art" role="img" aria-label="Specials banner photo of a shopper beside an up to 20 percent off offer">
      <div class="deal">20%</div>
      <div class="more">Learn More</div>
    </div>
  </div>

  <div class="panel account">
    <div class="inner">
      <div class="portrait" role="img" aria-label="Customer profile photo"></div>
      <div class="info">
        <h3>Welcome, Minh</h3>
        <span class="link">My Profile</span><span class="link">Settings</span>
        <div class="cart">My Cart</div>
        <div class="items">4 Items<br><em>(Show Details)</em><br>$34,023</div>
        <div class="checkout">Express Checkout</div>
      </div>
    </div>
  </div>

  <nav class="bar catnav">
    <a>Lorem</a><a>Ipsum</a><a>Proin</a><a>Gravida</a><a class="active">Main Category</a><a>Nibhvel</a><a>Auctor</a><a>Aliquet</a><a>Aenean</a>
  </nav>
  <nav class="bar subnav">
    <a>Ipsum</a><a>Nec sagittis</a><a>Sem nibh id</a><a>Duis sed</a><a>Odio sit</a><a>Amet nibh</a><a class="active">Sub Category</a><a>Vulputate</a><a>Cursus</a><a>Amet</a>
  </nav>

  <div class="crumbs">Home &gt; Main Category &gt; <span>Sub Category</span></div>
  <h1 class="title">Sub Category</h1>

  <section class="section featured">
    <h2>Featured Products</h2>
    <div class="row">
      <div class="item"><div class="shot"><div class="bottle green" role="img" aria-label="Green shampoo bottle"></div></div><div class="name">Product Name</div><div class="meta"><span>500ml</span><span>$2.59</span></div><div class="order"><span class="qty-btn">−</span><span class="qty">1</span><span class="qty-btn">+</span><span class="add" aria-label="Add to cart"><svg viewBox="0 0 16 16" fill="none" stroke="#fff" stroke-width="1.6"><path d="M1 2h2.5l1.8 8h8l1.5-5.5H4.2"/><circle cx="6.5" cy="13.5" r="1.2"/><circle cx="12" cy="13.5" r="1.2"/></svg></span></div></div>
      <div class="item"><div class="shot"><div class="bottle blue" role="img" aria-label="Blue and white shampoo bottle"></div></div><div class="name">Product Name</div><div class="meta"><span>500ml</span><span>$2.59</span></div><div class="order"><span class="qty-btn">−</span><span class="qty">1</span><span class="qty-btn">+</span><span class="add" aria-label="Add to cart"><svg viewBox="0 0 16 16" fill="none" stroke="#fff" stroke-width="1.6"><path d="M1 2h2.5l1.8 8h8l1.5-5.5H4.2"/><circle cx="6.5" cy="13.5" r="1.2"/><circle cx="12" cy="13.5" r="1.2"/></svg></span></div></div>
      <div class="item"><div class="shot"><div class="bottle white" role="img" aria-label="White shampoo bottle"></div></div><div class="name">Product Name</div><div class="meta"><span>500ml</span><span>$2.59</span></div><div class="order"><span class="qty-btn">−</span><span class="qty">1</span><span class="qty-btn">+</span><span class="add" aria-label="Add to cart"><svg viewBox="0 0 16 16" fill="none" stroke="#fff" stroke-width="1.6"><path d="M1 2h2.5l1.8 8h8l1.5-5.5H4.2"/><circle cx="6.5" cy="13.5" r="1.2"/><circle cx="12" cy="13.5" r="1.2"/></svg></span></div></div>
      <div class="item"><div class="shot"><div class="bottle white" role="img" aria-label="White shampoo bottle"></div></div><div class="name">Product Name</div><div class="meta"><span>500ml</span><span>$2.59</span></div><div class="order"><span class="qty-btn">−</span><span class="qty">1</span><span class="qty-btn">+</span><span class="add" aria-label="Add to cart"><svg viewBox="0 0 16 16" fill="none" stroke="#fff" stroke-width="1.6"><path d="M1 2h2.5l1.8 8h8l1.5-5.5H4.2"/><circle cx="6.5" cy="13.5" r="1.2"/><circle cx="12" cy="13.5" r="1.2"/></svg></span></div></div>
      <div class="item"><div class="shot"><div class="bottle pink" role="img" aria-label="Pink shampoo bottle"></div></div><div class="name">Product Name</div><div class="meta"><span>500ml</span><span>$2.59</span></div><div class="order"><span class="qty-btn">−</span><span class="qty">1</span><span class="qty-btn">+</span><span class="add" aria-label="Add to cart"><svg viewBox="0 0 16 16" fill="none" stroke="#fff" stroke-width="1.6"><path d="M1 2h2.5l1.8 8h8l1.5-5.5H4.2"/><circle cx="6.5" cy="13.5" r="1.2"/><circle cx="12" cy="13.5" r="1.2"/></svg></span></div></div>
    </div>
  </section>

  <section class="section latest">
    <h2>Latest Arrivals <small>(see all)</small></h2>
    <div class="row">
      <div class="item"><div class="shot"><div class="bottle green" role="img" aria-label="Green shampoo bottle"></div></div><div class="name">Product Name</div><div class="meta"><span>500ml</span><span>$2.59</span></div><div class="order"><span class="qty-btn">−</span><span class="qty">1</span><span class="qty-btn">+</span><span class="add" aria-label="Add to cart"><svg viewBox="0 0 16 16" fill="none" stroke="#fff" stroke-width="1.6"><path d="M1 2h2.5l1.8 8h8l1.5-5.5H4.2"/><circle cx="6.5" cy="13.5" r="1.2"/><circle cx="12" cy="13.5" r="1.2"/></svg></span></div></div>
      <div class="item"><div class="shot"><div class="bottle blue" role="img" aria-label="Blue and white shampoo bottle"></div></div><div class="name">Product Name</div><div class="meta"><span>500ml</span><span>$2.59</span></div><div class="order"><span class="qty-btn">−</span><span class="qty">1</span><span class="qty-btn">+</span><span class="add" aria-label="Add to cart"><svg viewBox="0 0 16 16" fill="none" stroke="#fff" stroke-width="1.6"><path d="M1 2h2.5l1.8 8h8l1.5-5.5H4.2"/><circle cx="6.5" cy="13.5" r="1.2"/><circle cx="12" cy="13.5" r="1.2"/></svg></span></div></div>
      <div class="item"><div class="shot"><div class="bottle white" role="img" aria-label="White shampoo bottle"></div></div><div class="name">Product Name</div><div class="meta"><span>500ml</span><span>$2.59</span></div><div class="order"><span class="qty-btn">−</span><span class="qty">1</span><span class="qty-btn">+</span><span class="add" aria-label="Add to cart"><svg viewBox="0 0 16 16" fill="none" stroke="#fff" stroke-width="1.6"><path d="M1 2h2.5l1.8 8h8l1.5-5.5H4.2"/><circle cx="6.5" cy="13.5" r="1.2"/><circle cx="12" cy="13.5" r="1.2"/></svg></span></div></div>
      <div class="item"><div class="shot"><div class="bottle white" role="img" aria-label="White shampoo bottle"></div></div><div class="name">Product Name</div><div class="meta"><span>500ml</span><span>$2.59</span></div><div class="order"><span class="qty-btn">−</span><span class="qty">1</span><span class="qty-btn">+</span><span class="add" aria-label="Add to cart"><svg viewBox="0 0 16 16" fill="none" stroke="#fff" stroke-width="1.6"><path d="M1 2h2.5l1.8 8h8l1.5-5.5H4.2"/><circle cx="6.5" cy="13.5" r="1.2"/><circle cx="12" cy="13.5" r="1.2"/></svg></span></div></div>
      <div class="item"><div class="shot"><div class="bottle pink" role="img" aria-label="Pink shampoo bottle"></div></div><div class="name">Product Name</div><div class="meta"><span>500ml</span><span>$2.59</span></div><div class="order"><span class="qty-btn">−</span><span class="qty">1</span><span class="qty-btn">+</span><span class="add" aria-label="Add to cart"><svg viewBox="0 0 16 16" fill="none" stroke="#fff" stroke-width="1.6"><path d="M1 2h2.5l1.8 8h8l1.5-5.5H4.2"/><circle cx="6.5" cy="13.5" r="1.2"/><circle cx="12" cy="13.5" r="1.2"/></svg></span></div></div>
    </div>
    <div class="row">
      <div class="item"><div class="shot"><div class="bottle green" role="img" aria-label="Green shampoo bottle"></div></div><div class="name">Product Name</div><div class="meta"><span>500ml</span><span>$2.59</span></div><div class="order"><span class="qty-btn">−</span><span class="qty">1</span><span class="qty-btn">+</span><span class="add" aria-label="Add to cart"><svg viewBox="0 0 16 16" fill="none" stroke="#fff" stroke-width="1.6"><path d="M1 2h2.5l1.8 8h8l1.5-5.5H4.2"/><circle cx="6.5" cy="13.5" r="1.2"/><circle cx="12" cy="13.5" r="1.2"/></svg></span></div></div>
      <div class="item"><div class="shot"><div class="bottle blue" role="img" aria-label="Blue and white shampoo bottle"></div></div><div class="name">Product Name</div><div class="meta"><span>500ml</span><span>$2.59</span></div><div class="order"><span class="qty-btn">−</span><span class="qty">1</span><span class="qty-btn">+</span><span class="add" aria-label="Add to cart"><svg viewBox="0 0 16 16" fill="none" stroke="#fff" stroke-width="1.6"><path d="M1 2h2.5l1.8 8h8l1.5-5.5H4.2"/><circle cx="6.5" cy="13.5" r="1.2"/><circle cx="12" cy="13.5" r="1.2"/></svg></span></div></div>
      <div class="item"><div class="shot"><div class="bottle white" role="img" aria-label="White shampoo bottle"></div></div><div class="name">Product Name</div><div class="meta"><span>500ml</span><span>$2.59</span></div><div class="order"><span class="qty-btn">−</span><span class="qty">1</span><span class="qty-btn">+</span><span class="add" aria-label="Add to cart"><svg viewBox="0 0 16 16" fill="none" stroke="#fff" stroke-width="1.6"><path d="M1 2h2.5l1.8 8h8l1.5-5.5H4.2"/><circle cx="6.5" cy="13.5" r="1.2"/><circle cx="12" cy="13.5" r="1.2"/></svg></span></div></div>
      <div class="item"><div class="shot"><div class="bottle white" role="img" aria-label="White shampoo bottle"></div></div><div class="name">Product Name</div><div class="meta"><span>500ml</span><span>$2.59</span></div><div class="order"><span class="qty-btn">−</span><span class="qty">1</span><span class="qty-btn">+</span><span class="add" aria-label="Add to cart"><svg viewBox="0 0 16 16" fill="none" stroke="#fff" stroke-width="1.6"><path d="M1 2h2.5l1.8 8h8l1.5-5.5H4.2"/><circle cx="6.5" cy="13.5" r="1.2"/><circle cx="12" cy="13.5" r="1.2"/></svg></span></div></div>
      <div class="item"><div class="shot"><div class="bottle pink" role="img" aria-label="Pink shampoo bottle"></div></div><div class="name">Product Name</div><div class="meta"><span>500ml</span><span>$2.59</span></div><div class="order"><span class="qty-btn">−</span><span class="qty">1</span><span class="qty-btn">+</span><span class="add" aria-label="Add to cart"><svg viewBox="0 0 16 16" fill="none" stroke="#fff" stroke-width="1.6"><path d="M1 2h2.5l1.8 8h8l1.5-5.5H4.2"/><circle cx="6.5" cy="13.5" r="1.2"/><circle cx="12" cy="13.5" r="1.2"/></svg></span></div></div>
    </div>
    <div class="row">
      <div class="item"><div class="shot"><div class="bottle green" role="img" aria-label="Green shampoo bottle"></div></div></div>
      <div class="item"><div class="shot"><div class="bottle blue" role="img" aria-label="Blue and white shampoo bottle"></div></div></div>
      <div class="item"><div class="shot"><div class="bottle white" role="img" aria-label="White shampoo bottle"></div></div></div>
      <div class="item"><div class="shot"><div class="bottle white" role="img" aria-label="White shampoo bottle"></div></div></div>
      <div class="item"><div class="shot"><div class="bottle pink" role="img" aria-label="Pink shampoo bottle"></div></div></div>
    </div>
  </section>
</div>
</body>
</html>
```